Design für Geburtskarte A6 hoch, Klappkarte
Zielgruppe
Ich bin Fotograf und habe mich auf Schwangerschafts- und Neugeborenenfotografie spezialisiert. Meine Zielgruppe sind schwangere Frauen im letzten Drittel der Schwangerschaft und frisch gewordene Eltern.
Aufgabenstellung
- sehr schlichtes Design, in der Anlage finden Sie zwei der meist verkauften Karten damit Sie sich vom Stil eine Vorstellung machen können
- Lieferung als offene Indesign 5.5 Datei (so das die Farben, Texte, .... angepasst werden können)
- 2-3 Bilder (querformat) sollen in das Design eingearbeitet werden können
- Die Karten werden von mir nachher als fertig gedruckte Karte an meine Kunden verkauft, dies bitte ich zu berücksichtigen
- ich möchte die Karten so nutzen können das sowohl Geburtskarten für Jungs wie auch für Mädels erstellt werden können
- Format: Din A6 (geschlossen 105x148mm), Klappkarte, hoch, 3mm Beschnitt

```html
<!DOCTYPE html>
<html lang="de">
<head>
<meta charset="utf-8">
<title>Geburtskarte – Lukas ist da</title>
<link href="https://fonts.googleapis.com/css2?family=Mulish:wght@400;600&family=Shadows+Into+Light&family=Gochi+Hand&display=swap" rel="stylesheet">
<style>
  :root {
    --bg: #dcdcdc;
    --teal: #7eaaab;
    --teal-light: #a6c6c6;
    --paper: #ffffff;
    --ink: #2b2b2b;
    --photo-light: #e4e4e2;
    --photo-mid: #a89a88;
    --photo-dark: #6f6559;
  }
  * { margin: 0; padding: 0; box-sizing: border-box; }
  html, body { width: 1200px; height: 800px; overflow: hidden; background: var(--bg); }
  body { font-family: "Mulish", sans-serif; color: var(--ink); position: relative; }

  .spread {
    position: absolute; left: 90px; top: 175px;
    width: 640px; height: 451px; display: flex;
    box-shadow: 0 10px 30px rgba(0,0,0,.12);
  }
  .panel { width: 320px; height: 451px; position: relative; }

  .panel--facts { background: var(--teal); color: var(--paper); }
  .brand {
    position: absolute; top: 28px; right: 28px;
    width: 84px; height: 84px; border-radius: 50%;
    background: rgba(255,255,255,.28);
    display: flex; flex-direction: column; align-items: center; justify-content: center;
  }
  .brand__name { font-family: "Mulish", sans-serif; font-size: 14px; font-weight: 600; }
  .brand__sub { font-size: 7px; letter-spacing: .5px; margin-top: 2px; }

  .facts { position: absolute; left: 0; right: 0; top: 150px; display: flex; flex-direction: column; gap: 34px; align-items: center; }
  .fact { display: flex; align-items: center; gap: 18px; width: 170px; }
  .fact svg { width: 40px; height: 40px; flex: none; }
  .fact__value { font-size: 13px; line-height: 1.45; letter-spacing: .3px; }

  .panel--message { background: var(--paper); padding: 120px 36px 0; text-align: center; }
  .headline { font-family: "Shadows Into Light", cursive; color: var(--teal); font-size: 40px; font-weight: 400; margin-bottom: 18px; }
  .message { font-size: 10.5px; line-height: 1.6; margin-bottom: 12px; }
  .signature { font-family: "Gochi Hand", cursive; font-size: 17px; margin-top: 16px; }

  .cover {
    position: absolute; left: 790px; top: 175px;
    width: 320px; height: 451px; background: var(--paper);
    box-shadow: 0 10px 30px rgba(0,0,0,.12);
  }
  .cover__photo {
    position: absolute; left: 0; top: 0; width: 320px; height: 380px;
    background:
      radial-gradient(ellipse at 45% 65%, var(--photo-mid) 0%, var(--photo-dark) 45%, transparent 75%),
      linear-gradient(160deg, var(--photo-light) 0%, #c9c4bc 50%, var(--photo-mid) 100%);
  }
  .cover__badge {
    position: absolute; top: 30px; right: 24px;
    width: 104px; height: 104px; border-radius: 50%;
    background: var(--teal); color: var(--paper);
    display: flex; flex-direction: column; align-items: center; justify-content: center; text-align: center;
  }
  .cover__name { font-family: "Shadows Into Light", cursive; font-size: 19px; line-height: 1.05; }
  .cover__date { font-size: 8px; margin-top: 5px; letter-spacing: .3px; }
</style>
</head>
<body>
  <section class="spread">
    <div class="panel panel--facts">
      <div class="brand">
        <span class="brand__name">Lichtfang</span>
        <span class="brand__sub">Fotografie</span>
      </div>
      <div class="facts">
        <div class="fact">
          <svg viewBox="0 0 40 40" fill="none" stroke="currentColor" stroke-width="1.5">
            <circle cx="20" cy="20" r="17"/><circle cx="20" cy="20" r="13"/>
            <path d="M20 12v8l-4 3" stroke-linecap="round"/>
          </svg>
          <span class="fact__value">21.01.2016<br>03:12 Uhr</span>
        </div>
        <div class="fact">
          <svg viewBox="0 0 40 40" fill="none" stroke="currentColor" stroke-width="1.5">
            <path d="M6 12h28M10 12v-4h20v4"/>
            <path d="M9 14h22l-2 20H11z" stroke-linejoin="round"/>
            <path d="M15 22a5 5 0 0 1 10 0"/><path d="M20 22l2-3" stroke-linecap="round"/>
          </svg>
          <span class="fact__value">3000 g</span>
        </div>
        <div class="fact">
          <svg viewBox="0 0 40 40" fill="none" stroke="currentColor" stroke-width="1.5">
            <rect x="4" y="14" width="32" height="12" rx="1"/>
            <path d="M9 14v5M14 14v3M19 14v5M24 14v3M29 14v5"/>
          </svg>
          <span class="fact__value">52 cm</span>
        </div>
      </div>
    </div>
    <div class="panel panel--message">
      <h1 class="headline">Lukas ist da</h1>
      <p class="message">Das Menschlein, dass zu unserem Glück noch fehlt, liegt endlich in unseren Armen. Lukas ist stolze 45 cm gross. Er wiegt 2970 Gramm und ist kerngesund.</p>
      <p class="message">Während einer kleinen Autofahrt hatte er plötzlich den Drang ein Teil der Welt zu werden und ließ uns bis 02:00 Uhr in der Nacht keine Ruhe mehr</p>
      <p class="signature">Der stolze Papa mit der Mama</p>
    </div>
  </section>

  <section class="cover">
    <div class="cover__photo" role="img" aria-label="Foto: schlafendes Neugeborenes mit Strickmütze auf einem Fell in einem Korb, zugedeckt mit grauer Strickdecke"></div>
    <div class="cover__badge">
      <span class="cover__name">Lukas<br>Benedikt</span>
      <span class="cover__date">03. Juli 2015</span>
    </div>
  </section>
</body>
</html>
```